Website for a health information tech company

I need a website for a new startup company, Velorim Health, Inc. that specializes in healthcare information technology. Velorim Health is a monitoring system that uses wearable sensors and predictive algorithms to detect when an elderly persons health is declining and triggers progressively higher levels of interventions.

The site needs to be very simple, elegant and initially will have minimal information as company and product is still under development and is in a stealth mode. I like the lumotreva.com website as it has a "single page" look and feel with sliding vertical sections. Ideally the sections would be "Home", "Technology", "Customers", "News", "About Us" and "Contact Us". The contact us should have a contact form that gets sent to an email address.

I have a couple of example sites that my site should take inspiration from (lumotreva.com and bixendale.com). I would like a WordPress backend so I can easily update content so the winning design should be easily importable or setup into Wordpress.

Target Market(s)

Investors, Customers (Doctors, Patients, Health Insurance companies, Hospital directors)

Industry/Entity Type

Healthcare

Requirements
Must have
• top horizontal menu that gets repeated on each vertical slide. Should have animated vertical slides. Must be viewable on any device (iPad, Android Tablets) correctly and must render correctly on different screen sizes. Must be viewable in all popular browsers. Must work well with touchscreen devices such as iPad, iPhone, Android tablets and phones.
Must have a content management system backend such as WordPress so I can edit/update content and in future add additional sections, images etc.

See attached company logo so colors must be complimentary to the logo colors. Feel free to use the logo colors as web site theme colors if it makes sense.
Nice to have
• Nice subtle textured background like linen or leather.
Should not have
• Not looking for traditional web site design with nav bars on left etc
Should not feel like a traditional web site where you click a link and another page loads. It must be animated slide into a different section. No flash or any other technology that requires plug ins.

```html
<!DOCTYPE html>
<html lang="en">
<head>
<meta charset="utf-8">
<title>Velorim Health – Technology</title>
<link rel="stylesheet" href="https://fonts.googleapis.com/css2?family=PT+Sans:wght@400;700&display=swap">
<style>
  :root {
    --orange: #f26a1b;
    --orange-light: #f7941e;
    --orange-dark: #c85a12;
    --ink: #1f1f1f;
    --muted: #5a5a5a;
    --soft: #666666;
    --header-bg: #efefef;
    --tab-bg: #e2e2e2;
    --footer-bg: #e6e6e6;
    --player-frame: #000000;
    --player-screen: #3d3d3d;
    --player-bar: #8a8a8a;
    --social-1: #3b5a9a;
    --social-2: #4fc3f0;
    --social-3: #3a9fd6;
  }
  * { box-sizing: border-box; margin: 0; padding: 0; }
  html, body { width: 1200px; height: 801px; overflow: hidden; }
  body {
    position: relative;
    font-family: "PT Sans", Arial, sans-serif;
    color: var(--ink);
    background: #d8d8d8;
  }
  .hero-photo {
    position: absolute; inset: 0;
    background:
      radial-gradient(ellipse at 30% 55%, rgba(255,255,255,0.55), rgba(255,255,255,0) 45%),
      radial-gradient(ellipse at 15% 90%, rgba(255,255,255,0.7), rgba(255,255,255,0) 35%),
      linear-gradient(180deg, #d2d2d2 0%, #c4c4c4 40%, #d6d6d6 75%, #e4e4e4 100%);
  }
  .site-header {
    position: absolute; left: 0; top: 0; width: 1200px; height: 143px;
    background: rgba(242,242,242,0.92);
    border-bottom: 1px solid #ffffff;
  }
  .brand {
    position: absolute; left: 89px; top: 92px;
    display: flex; align-items: center; gap: 10px;
    font-size: 26px; font-weight: 700; color: var(--orange);
  }
  .brand-dot { width: 22px; height: 22px; border-radius: 50%; background: var(--orange); }
  .account-tab {
    position: absolute; left: 896px; top: 0; width: 205px; height: 52px;
    background: var(--tab-bg); border-radius: 0 0 10px 10px;
    display: flex; align-items: center; justify-content: center; gap: 14px;
    font-size: 18px; color: var(--orange-dark);
  }
  .main-nav {
    position: absolute; left: 532px; top: 73px; width: 668px; height: 43px;
    background: linear-gradient(180deg, var(--orange-light), var(--orange));
    border-radius: 4px 0 0 4px;
    display: flex; align-items: center; padding-left: 24px; gap: 13px;
    font-size: 18px; color: #000;
  }
  .main-nav .sep { font-size: 14px; }
  .main-nav .is-active { color: #fff; }
  .section-title {
    position: absolute; left: 93px; top: 291px;
    font-size: 27px; font-weight: 700; color: var(--orange);
  }
  .section-text {
    position: absolute; left: 93px; top: 334px; width: 504px;
    font-size: 15.5px; line-height: 29px; text-align: justify; color: var(--ink);
  }
  .mark-faint {
    position: absolute; left: 80px; top: 560px;
    display: flex; align-items: center; gap: 6px;
    font-size: 17px; font-weight: 700; color: #8e8e8e;
  }
  .mark-faint .brand-dot { width: 14px; height: 14px; background: #9a9a9a; }
  .teaser {
    position: absolute; left: 240px; top: 550px; width: 260px;
    font-size: 16px; line-height: 29px; color: var(--soft);
  }
  .video-player {
    position: absolute; left: 634px; top: 284px; width: 456px; height: 283px;
    background: var(--player-frame); border: 3px solid #fff; border-radius: 7px;
  }
  .video-screen {
    position: absolute; left: 8px; top: 8px; right: 8px; bottom: 8px;
    background: var(--player-screen); border-radius: 4px;
  }
  .video-screen .screen-name {
    position: absolute; left: 0; right: 0; top: 176px; text-align: center;
    font-size: 34px; font-weight: 700; color: #555;
  }
  .video-screen svg { position: absolute; left: 0; top: 0; }
  .site-footer {
    position: absolute; left: 0; top: 662px; width: 1200px; height: 139px;
    background: rgba(232,232,232,0.85); border-top: 1px solid #ffffff;
  }
  .footer-nav {
    position: absolute; left: 92px; top: 36px;
    font-size: 13px; color: var(--muted); display: flex; gap: 8px;
  }
  .copyright { position: absolute; left: 92px; top: 70px; font-size: 13px; color: var(--muted); }
  .social { position: absolute; left: 986px; top: 45px; display: flex; gap: 5px; }
  .social span { width: 33px; height: 33px; border-radius: 50%; display: block; }
</style>
</head>
<body>
  <div class="hero-photo" role="img" aria-label="Greyscale photo of a businesswoman touching a holographic interface with a sky and world map backdrop"></div>

  <header class="site-header">
    <div class="brand"><span class="brand-dot"></span>Velorim Health</div>
    <div class="account-tab"><span>REGISTER</span><span>::</span><span>LOGIN</span></div>
    <nav class="main-nav">
      <span>Home</span><span class="sep">::</span>
      <span class="is-active">Technology</span><span class="sep">::</span>
      <span>Customers</span><span class="sep">::</span>
      <span>About Us</span><span class="sep">::</span>
      <span>Contact Us</span>
    </nav>
  </header>

  <main>
    <h1 class="section-title">Technology</h1>
    <p class="section-text">An intelligent machine learning system that uses activity and behavior pattern sensors in conjunction with observatory and interrogatory clinical scoring to predict when a functional decline in health is occurring and trigger interventions from the circles of care surrounding an elderly person from family and friends to clinicians.</p>

    <div class="mark-faint"><span class="brand-dot"></span>Velorim Health</div>
    <p class="teaser">Maecenas semlar sem, molestie sed faucibus eu, viverra eget ante...</p>

    <div class="video-player">
      <div class="video-screen">
        <div class="screen-name">Velorim Health</div>
        <svg width="434" height="261" viewBox="0 0 434 261">
          <circle cx="216" cy="117" r="32" fill="#1e1e1e"/>
          <path d="M207 102 L229 117 L207 132 Z" fill="#ffffff"/>
          <rect x="14" y="228" width="386" height="4" fill="var(--player-bar)"/>
          <rect x="408" y="225" width="3" height="9" fill="var(--player-bar)"/>
          <rect x="414" y="225" width="3" height="9" fill="var(--player-bar)"/>
        </svg>
      </div>
    </div>
  </main>

  <footer class="site-footer">
    <nav class="footer-nav">
      <span>Home</span><span>|</span><span>Technology</span><span>|</span><span>Customers</span><span>|</span><span>About Us</span><span>|</span><span>Contact Us</span>
    </nav>
    <p class="copyright">Copyright © 2013 &nbsp;www.velorimhealth.com &nbsp; All rights reserved.</p>
    <div class="social">
      <span style="background:var(--social-1)"></span>
      <span style="background:var(--social-2)"></span>
      <span style="background:var(--social-3)"></span>
    </div>
  </footer>
</body>
</html>
```